Diverse, up-scale salon needs eye-catching, unique business cards.

We are looking for a unique business card design for our stylist but that can also be multi functional and used for appointment reminder and referrals. I will need a design in a format that I can modify names and titles going forward. In the past we have had a dark background with the logo on one side, and stylist and contact information on the other but we are open to all ideas. I have included our mission statement as well as branded colors below. The statement doesn't need to go on the card, it's just a reference for target market. We need space for the stylists name, title, instagram handle and then the salons phone number, website and address. I am also open to adding a spot for a qr code linked to the stylist instagram or the salon booking link.

primary brand colors:
#333333 #233415 #36502a #93874a #000000
Mission statement:
Vessolin Hair Studio, a high-end salon located in the lively Downtown Farmington, Michigan, is committed to providing exceptional services in a welcoming and relaxed environment to meet the needs of our diverse clientele.
Our salon specializes in contemporary custom haircuts, coloring, extensions, and barbering and beard grooming services. Our team of skilled stylists is passionate and inventive in their hair styling techniques. At the heart of our salon are values centered on quality, innovation, creativity, and above all, comfort. These core values are evident in every appointment across our customizable array of services.
Our goal is to establish a benchmark for exceptional hair care for every human.
Website: www.vessolinhairstudio.example
instagram: @vessolinhairstudio
address: 41782 Pelham Crest Rd, Harlow Ridge MI
phone: 555-613-4087

Industry/Entity Type

Hair Salon

Contact Information for Business Card

Stylist name, title, phone, instagram, website, address, (optional qr code)

Requirements
Should not have
• Does not need mission statement on the card.

```html
<!DOCTYPE html>
<html lang="en">
<head>
<meta charset="utf-8">
<title>Vessolin Hair Studio – Business Card</title>
<link rel="stylesheet" href="https://fonts.googleapis.com/css2?family=Arimo:wght@400;700&display=swap">
<style>
  :root {
    --backdrop: #2a2a2b;
    --card: #1c1d1f;
    --gold: #a08d45;
    --ink: #ffffff;
    --rule: #cfcfcf;
  }
  * { box-sizing: border-box; margin: 0; padding: 0; }
  html, body {
    width: 1200px; height: 1108px; overflow: hidden;
    background: var(--backdrop);
    font-family: "Arimo", Arial, sans-serif;
  }
  .stage {
    width: 1200px; height: 1108px;
    display: flex; justify-content: center; align-items: center; gap: 100px;
  }
  .card {
    width: 400px; height: 640px;
    background: var(--card);
    border-radius: 26px;
    display: flex; flex-direction: column; align-items: center;
    box-shadow: 0 16px 40px rgba(0,0,0,.45);
  }
  .brand-mark {
    display: flex; flex-direction: column; align-items: center; gap: 14px;
  }
  .brand-mark .ring {
    width: 120px; height: 120px; border: 4px solid var(--gold); border-radius: 50%;
  }
  .brand-mark .brand-name {
    color: var(--gold); font-weight: 700; font-size: 20px;
    letter-spacing: 3px; text-transform: uppercase;
  }
  .card--front { padding-top: 60px; }
  .card--back { justify-content: center; }
  .card--back .ring { width: 190px; height: 190px; border-width: 5px; }
  .card--back .brand-name { font-size: 26px; }

  .person { margin-top: 34px; text-align: center; }
  .person-name {
    color: var(--gold); font-weight: 700; font-size: 26px; letter-spacing: 1px;
    text-transform: uppercase;
  }
  .person-title { color: var(--ink); font-size: 20px; margin-top: 4px; }

  .icon-rule {
    width: 320px; margin-top: 16px;
    display: flex; align-items: center; gap: 8px;
  }
  .icon-rule .line { flex: 1; height: 1px; background: var(--rule); }
  .icon {
    width: 28px; height: 28px; border-radius: 5px; background: var(--gold);
    display: flex; align-items: center; justify-content: center;
  }
  .contact {
    margin-top: 14px; text-align: center; color: var(--ink);
    font-size: 20px; line-height: 27px;
  }
  .rule { width: 320px; height: 1px; background: var(--rule); margin-top: 14px; }
  .address {
    margin-top: 12px; text-align: center; color: var(--ink);
    font-size: 20px; line-height: 27px;
  }
</style>
</head>
<body>
<main class="stage">
  <section class="card card--front">
    <div class="brand-mark">
      <div class="ring"></div>
      <div class="brand-name">Vessolin Hair Studio</div>
    </div>
    <div class="person">
      <div class="person-name">Marcus Delane</div>
      <div class="person-title">Manager</div>
    </div>
    <div class="icon-rule">
      <span class="line"></span>
      <span class="icon" aria-label="Phone">
        <svg width="18" height="18" viewBox="0 0 24 24"><path d="M6.6 10.8a15 15 0 0 0 6.6 6.6l2.2-2.2a1 1 0 0 1 1-.25 11.4 11.4 0 0 0 3.6.6 1 1 0 0 1 1 1V20a1 1 0 0 1-1 1A17 17 0 0 1 3 4a1 1 0 0 1 1-1h3.5a1 1 0 0 1 1 1c0 1.25.2 2.45.6 3.6a1 1 0 0 1-.25 1z" fill="#1c1d1f"/></svg>
      </span>
      <span class="icon" aria-label="Social handle"></span>
      <span class="icon" aria-label="Website">
        <svg width="18" height="18" viewBox="0 0 24 24" fill="none" stroke="#1c1d1f" stroke-width="2"><circle cx="12" cy="12" r="9"/><path d="M3 12h18M12 3c3 3 3 15 0 18M12 3c-3 3-3 15 0 18"/></svg>
      </span>
      <span class="line"></span>
    </div>
    <div class="contact">
      <div>555-613-4087</div>
      <div>@vessolinhairstudio</div>
      <div>www.vessolinhairstudio.example</div>
    </div>
    <div class="rule"></div>
    <div class="address">
      <div>41782 Pelham Crest Rd</div>
      <div>Harlow Ridge MI</div>
    </div>
  </section>

  <section class="card card--back">
    <div class="brand-mark">
      <div class="ring"></div>
      <div class="brand-name">Vessolin Hair Studio</div>
    </div>
  </section>
</main>
</body>
</html>
```